we can communicate on this, but i want to follow the approach we took on Pellew|Marsh & Quinlan but i feel the card front needs the black background and the platinum and gold logo. The back? I am open. we can use the same info from PM&Q. Velmont Arc is an enhanced equity investment fund - basically a very exclusive boutique hedge fund that uses only stock options. very advanced things. hope you are interested

Contact Information for Business Card

Dr. Lewis T. Brennick, CFA
Scientifique de fusée financière
701.555.0143
LTBquant47@mailvantor.com

4718 Willow Creek Bend W.
West Fargo, ND 58078

No web site

Colors

Designer to choose colors to be used in the design.

Requirements
Nice to have
• I tend to prefer the most visible applications of the logo to include logo and name, the logo version with a black background and the gold and platinum components separated by the black. I see this working well for a single side (logo and name - this is card front to me).
• I am fairly open to other treatments on the reverse side with the data. To me, it makes sense to have a different color rendition of the logo on the reverse and it may be a muted black tone on tone or an oversized portion that would have spot UV. Or, the reverse may play with colors and layout
Should not have
• Other colors = no no
• Decorative font

```html
<!DOCTYPE html>
<html lang="en">
<head>
<meta charset="UTF-8">
<title>Velmont Arc – Business Cards</title>
<link rel="stylesheet" href="https://fonts.googleapis.com/css2?family=Montserrat:wght@400;500;700;800&display=swap">
<style>
  :root {
    --stage: #1c1c1f;
    --card-black: #050505;
    --paper-text: #f4f4f4;
    --gold: #c9a227;
    --gold-light: #e3c45a;
    --gold-deep: #9c7b17;
    --platinum: #c8c8cc;
  }
  * { box-sizing: border-box; margin: 0; padding: 0; }
  html, body { width: 1200px; height: 800px; overflow: hidden; }
  body {
    background: var(--stage);
    font-family: "Montserrat", Arial, sans-serif;
    display: flex;
    align-items: center;
    justify-content: center;
    gap: 40px;
  }
  .card {
    width: 530px;
    height: 303px;
    border-radius: 18px;
    position: relative;
    overflow: hidden;
    background: var(--card-black);
    color: var(--paper-text);
    box-shadow: 0 0 0 1px #2a2a2e;
  }
  .brand-name {
    font-weight: 800;
    text-transform: uppercase;
    letter-spacing: 1px;
    line-height: 1;
    color: var(--paper-text);
  }

  /* Front: black with brand */
  .card--front {
    display: flex;
    flex-direction: column;
    align-items: center;
    justify-content: center;
    gap: 24px;
  }
  .card--front .brand-dot {
    width: 92px;
    height: 92px;
    border-radius: 50%;
    background: linear-gradient(135deg, var(--gold-light), var(--gold) 60%, var(--gold-deep));
  }
  .card--front .brand-name { font-size: 40px; }

  /* Back: black with details */
  .back-mark {
    position: absolute;
    right: 38px;
    top: 44px;
    width: 176px;
    height: 176px;
    border-radius: 50%;
    background: linear-gradient(135deg, var(--gold-light), var(--gold) 60%, var(--gold-deep));
  }
  .back-info {
    position: absolute;
    left: 36px;
    bottom: 28px;
    width: 270px;
  }
  .back-info .brand-name { font-size: 28px; margin-bottom: 20px; }
  .person-name {
    font-weight: 700;
    font-size: 14px;
    text-transform: uppercase;
    letter-spacing: 0.4px;
    white-space: nowrap;
  }
  .person-role {
    color: var(--gold);
    font-size: 12.5px;
    font-weight: 500;
    margin: 3px 0 14px;
    white-space: nowrap;
  }
  .address { font-size: 12px; line-height: 1.45; margin-bottom: 10px; }
  .contact-list { list-style: none; }
  .contact-list li {
    display: flex; align-items: center; gap: 8px;
    font-size: 12px; line-height: 1; margin-bottom: 6px;
    white-space: nowrap;
  }
  .contact-list li:last-child { margin-bottom: 0; }
  .contact-icon { width: 16px; height: 16px; flex: none; }
</style>
</head>
<body>
  <section class="card card--front" aria-label="Card front">
    <div class="brand-dot"></div>
    <div class="brand-name">Velmont Arc</div>
  </section>

  <section class="card card--back" aria-label="Card back">
    <div class="back-mark"></div>
    <div class="back-info">
      <div class="brand-name">Velmont Arc</div>
      <div class="person-name">Dr. Lewis T. Brennick, CFA</div>
      <div class="person-role">Scientifique de fusée financière</div>
      <div class="address">4718 Willow Creek Bend W.<br>West Fargo, ND 58078</div>
      <ul class="contact-list">
        <li>
          <svg class="contact-icon" viewBox="0 0 16 16" aria-hidden="true">
            <circle cx="8" cy="8" r="8" fill="#c9a227"/>
            <path d="M5.2 4.2l1.6-.4 1 2-1 .8a5 5 0 0 0 2.6 2.6l.8-1 2 1-.4 1.6c-3.6.3-6.9-3-6.6-6.6z" fill="#050505"/>
          </svg>
          701.555.0143
        </li>
        <li>
          <svg class="contact-icon" viewBox="0 0 16 16" aria-hidden="true">
            <circle cx="8" cy="8" r="8" fill="#c9a227"/>
            <rect x="4" y="5" width="8" height="6" fill="none" stroke="#050505" stroke-width="1.2"/>
            <path d="M4 5l4 3.4L12 5" fill="none" stroke="#050505" stroke-width="1.2"/>
          </svg>
          LTBquant47@mailvantor.com
        </li>
      </ul>
    </div>
  </section>
</body>
</html>
```